Website - Loretta Dubrow

I need a website that has multiple pages and easy for me to update pictures, content and blogs as an ongoing basis’s.
It will have videos and needs to be compatible to view easily and aesthetically on mobile phones.
Please refer to this website for inspiration www.quinnafernsby.com

Coding

Coded - Design and coding required

Number of Pages Required

5+ page

Other font styles liked:
• Refer to website provided as inspiration

Requirements
Must have
• Please use stock images for now to do design, but I will be providing all imagery, videos and content

```html
<!DOCTYPE html>
<html lang="en">
<head>
<meta charset="utf-8">
<title>Loretta Dubrow</title>
<link href="https://fonts.googleapis.com/css2?family=Poppins:wght@600;700&family=Roboto:wght@400;500;700&display=swap" rel="stylesheet">
<style>
:root{
  --ink:#0b0b0b;
  --white:#ffffff;
  --sand-1:#ead6cc;
  --sand-2:#f0dcd0;
  --body-grey:#6f6662;
  --footer:#404040;
  --footer-text:#e6e6e6;
  --rock-light:#c9a98f;
  --rock-blue:#7d86a3;
}
*{box-sizing:border-box;margin:0;padding:0}
html,body{width:1200px;height:3164px;overflow:hidden}
body{position:relative;font-family:"Roboto",Arial,sans-serif;background:var(--sand-1);color:var(--ink)}
.abs{position:absolute}
.heading{font-family:"Poppins",Arial,sans-serif;font-weight:700;text-transform:uppercase}

/* header & hero */
.hero{left:0;top:0;width:1200px;height:522px;
  background:linear-gradient(180deg,#b89b87 0%,#9c8f9f 22%,#c5a58b 42%,#8d8ea8 62%,#b59a85 80%,#6c5a4b 100%)}
.hero-portrait{left:720px;top:90px;width:300px;height:432px;border-radius:140px 140px 0 0;
  background:linear-gradient(180deg,#8a5a48 0%,#d98a8e 45%,#c98f83 75%,#5f4a3e 100%);opacity:.85}
.brand{left:113px;top:24px;font-family:"Roboto",Arial,sans-serif;font-weight:700;font-size:21px;color:var(--white);letter-spacing:.3px;text-transform:uppercase}
.nav{top:29px;font-weight:700;font-size:14px;color:var(--white);text-transform:uppercase;letter-spacing:.2px}
.social-ring{width:38px;height:38px;border:2px solid var(--white);border-radius:50%}
.hero-title{left:113px;top:182px;font-size:55px;color:var(--white);letter-spacing:.5px;line-height:1.1}
.hero-text{left:114px;top:256px;width:500px;font-size:15px;line-height:24px;color:var(--white)}
.btn{display:flex;align-items:center;gap:10px;height:49px;padding:0 20px;background:var(--ink);color:var(--white);font-weight:700;font-size:14px;text-transform:uppercase;border-radius:2px}
.btn svg{width:14px;height:14px}

/* about */
.about{left:0;top:522px;width:1200px;height:737px;background:var(--sand-1)}
.about-frame{left:112px;top:629px;width:455px;height:509px;background:#f1e3dc;padding:4px;box-shadow:0 2px 8px rgba(0,0,0,.15)}
.about-photo{width:100%;height:100%;background:linear-gradient(180deg,#a6b7c2 0%,#6d7f86 40%,#e27bb5 62%,#8d8580 100%)}
.about-title{left:647px;top:694px;font-size:38px}
.about-sub{left:646px;top:756px;font-size:20px;font-weight:600}
.about-text{left:647px;top:798px;width:420px;font-size:14.5px;line-height:27.5px;color:var(--body-grey)}

/* blog */
.blog{left:0;top:1259px;width:1200px;height:601px;background:var(--sand-2)}
.section-title{left:0;width:1200px;text-align:center;font-size:38px}
.card-photo{top:1423px;width:318px;height:220px}
.card-title{font-weight:500;font-size:15px;text-transform:uppercase}
.card-date{display:flex;align-items:center;gap:12px;font-weight:700;font-size:13.5px}
.card-text{width:290px;font-size:13.5px;line-height:21px;color:var(--body-grey)}

/* videos */
.videos{left:0;top:1860px;width:1200px;height:918px;background:var(--sand-1)}
.video-main{left:135px;top:2045px;width:931px;height:495px;background:linear-gradient(180deg,#3e3e3e 0%,#cfcfcf 30%,#b3b3b3 65%,#8e8e8e 100%)}
.play{left:562px;top:2254px;width:74px;height:74px;border-radius:50%;background:var(--white);box-shadow:0 3px 10px rgba(0,0,0,.3);display:flex;align-items:center;justify-content:center}
.thumb{width:149px;height:118px}

/* footer */
.footer{left:0;top:2778px;width:1200px;height:386px;background:var(--footer);color:var(--footer-text)}
.foot-head{top:2853px;font-weight:700;font-size:16px;color:var(--white);text-transform:uppercase}
.foot-text{font-size:14.5px;line-height:26px;color:var(--footer-text)}
.email{left:113px;top:2956px;width:185px;height:40px;background:var(--white);color:#888;font-size:13px;padding:12px 14px}
.signup{left:301px;top:2956px;width:99px;height:40px;background:#111;color:var(--white);font-weight:700;font-size:14px;display:flex;align-items:center;justify-content:center}
.foot-link{display:flex;align-items:center;gap:20px;font-size:14.5px;height:30px;color:var(--footer-text)}
.foot-link svg{width:10px;height:10px}
.divider{left:112px;top:3092px;width:976px;height:1px;background:#9a9a9a}
.copyright{left:0;top:3118px;width:1200px;text-align:center;font-size:14.5px;color:var(--footer-text)}
</style>
</head>
<body>

<!-- Hero -->
<section class="abs hero" role="img" aria-label="Sandstone rock backdrop with layered tan and blue bands"></section>
<div class="abs hero-portrait" role="img" aria-label="Photo of Loretta seated on sandstone rocks in a pink swimsuit"></div>
<div class="abs brand">Loretta Dubrow</div>
<div class="abs nav" style="left:648px">Home</div>
<div class="abs nav" style="left:716px">About</div>
<div class="abs nav" style="left:788px">Blog</div>
<div class="abs nav" style="left:850px">Stories</div>
<div class="abs nav" style="left:934px">Contact</div>
<div class="abs social-ring" style="left:1047px;top:18px" aria-label="Social profile"></div>

<h1 class="abs heading hero-title">Loretta Dubrow</h1>
<p class="abs hero-text">Lorem ipsum dolor sit amet, consectetur adipiscing elit, sed do eiusmod tempor incididunt ut labore et dolore magna aliqua.</p>
<a class="abs btn" style="left:114px;top:324px">Learn More
  <svg viewBox="0 0 16 16"><circle cx="8" cy="8" r="8" fill="#fff"/><path d="M5 8h5M8 5l3 3-3 3" stroke="#0b0b0b" stroke-width="2" fill="none"/></svg></a>

<!-- About -->
<section class="abs about"></section>
<div class="abs about-frame"><div class="about-photo" role="img" aria-label="Photo of Loretta in a pink dress on a lakeside jetty"></div></div>
<h2 class="abs heading about-title">About Me</h2>
<h3 class="abs heading about-sub" style="font-family:'Poppins',Arial,sans-serif">I Am Loretta Dubrow</h3>
<p class="abs about-text">Lorem ipsum dolor sit amet, consectetur adipiscing elit, sed do eiusmod tempor incididunt ut labore et dolore magna aliqua. Ut enim ad minim veniam, quis nostrud exercitation ullamco laboris nisi ut aliquip ex ea commodo consequat. Duis aute irure dolor in reprehenderit in voluptate velit esse cillum dolore eu fugiat nulla pariatur. Excepteur sint occaecat cupidatat non proident, sunt in culpa qui officia deserunt mollit anim id est laborum.</p>
<a class="abs btn" style="left:648px;top:1014px">Learn More
  <svg viewBox="0 0 16 16"><circle cx="8" cy="8" r="8" fill="#fff"/><path d="M5 8h5M8 5l3 3-3 3" stroke="#0b0b0b" stroke-width="2" fill="none"/></svg></a>

<!-- Blog -->
<section class="abs blog"></section>
<h2 class="abs heading section-title" style="top:1326px">Latest Blog</h2>

<div class="abs card-photo" style="left:107px;background:linear-gradient(135deg,#d8d8d8,#6a6a6a 60%,#bdbdbd)" role="img" aria-label="Black and white photo of Loretta posing in boots"></div>
<div class="abs card-photo" style="left:441px;background:linear-gradient(180deg,#e2ddd6,#9c6a4c 50%,#d9927e)" role="img" aria-label="Photo of Loretta smiling in a patterned top"></div>
<div class="abs card-photo" style="left:775px;background:linear-gradient(90deg,#e9ebec,#b9bfc3 45%,#3aa6a0 65%,#d6d8d8)" role="img" aria-label="Photo of Loretta in a teal dress by a doorway"></div>

<div class="abs card-title" style="left:128px;top:1670px">Lorem ipsum dolor sit amet cons</div>
<div class="abs card-title" style="left:462px;top:1670px">Lorem ipsum dolor sit amet cons</div>
<div class="abs card-title" style="left:796px;top:1670px">Lorem ipsum dolor sit amet cons</div>

<div class="abs card-date" style="left:129px;top:1701px"><svg width="13" height="13" viewBox="0 0 13 13"><rect x="1" y="2" width="11" height="10" fill="none" stroke="#222" stroke-width="1.4"/><path d="M1 5h11M4 1v3M9 1v3" stroke="#222" stroke-width="1.4"/></svg>APR 20 , 2021</div>
<div class="abs card-date" style="left:463px;top:1701px"><svg width="13" height="13" viewBox="0 0 13 13"><rect x="1" y="2" width="11" height="10" fill="none" stroke="#222" stroke-width="1.4"/><path d="M1 5h11M4 1v3M9 1v3" stroke="#222" stroke-width="1.4"/></svg>APR 20 , 2021</div>
<div class="abs card-date" style="left:797px;top:1701px"><svg width="13" height="13" viewBox="0 0 13 13"><rect x="1" y="2" width="11" height="10" fill="none" stroke="#222" stroke-width="1.4"/><path d="M1 5h11M4 1v3M9 1v3" stroke="#222" stroke-width="1.4"/></svg>APR 20 , 2021</div>

<p class="abs card-text" style="left:129px;top:1728px">Sed ut perspiciatis unde omnis iste natus error sit voluptatem accusantium doloremque</p>
<p class="abs card-text" style="left:463px;top:1728px">Sed ut perspiciatis unde omnis iste natus error sit voluptatem accusantium doloremque</p>
<p class="abs card-text" style="left:797px;top:1728px">Sed ut perspiciatis unde omnis iste natus error sit voluptatem accusantium doloremque</p>

<!-- Videos -->
<section class="abs videos"></section>
<h2 class="abs heading section-title" style="top:1940px">Our Videos</h2>
<div class="abs video-main" role="img" aria-label="Black and white video still of a dancer stretching in a studio"></div>
<div class="abs play"><svg width="46" height="46" viewBox="0 0 46 46"><circle cx="23" cy="23" r="22" fill="#0b0b0b"/><path d="M18 14l13 9-13 9z" fill="#fff"/></svg></div>

<div class="abs thumb" style="left:135px;top:2546px;background:linear-gradient(180deg,#6f8aa0,#c9b39e 55%,#b7c4dc)" role="img" aria-label="Video thumbnail of Loretta by the water"></div>
<div class="abs thumb" style="left:292px;top:2546px;background:linear-gradient(135deg,#5a3b2c,#b79a82 55%,#7ea4a4)" role="img" aria-label="Video thumbnail of Loretta taking a selfie"></div>
<div class="abs thumb" style="left:447px;top:2546px;background:linear-gradient(180deg,#e8e4df,#c9a8a0 55%,#e08aa5)" role="img" aria-label="Video thumbnail of Loretta in a kitchen"></div>
<div class="abs thumb" style="left:603px;top:2529px;background:linear-gradient(180deg,#5a5a5a,#cfcfcf 35%,#9a9a9a);box-shadow:0 3px 8px rgba(0,0,0,.25)" role="img" aria-label="Video thumbnail of the studio dance clip"></div>
<div class="abs thumb" style="left:760px;top:2546px;background:linear-gradient(180deg,#e7e6e2,#b8b4bd 50%,#d7cfc7)" role="img" aria-label="Video thumbnail of Loretta seated at home"></div>
<div class="abs thumb" style="left:917px;top:2546px;background:linear-gradient(180deg,#ede8e2,#cfc3b6 55%,#e7a48f)" role="img" aria-label="Video thumbnail of Loretta in a knit sweater"></div>

<!-- Footer -->
<footer class="abs footer"></footer>
<div class="abs foot-head" style="left:112px">Stay Connected</div>
<p class="abs foot-text" style="left:112px;top:2886px;width:340px">Lorem ipsum dolor sit ame consectetur adipiscing elit, sed do eiusmod</p>
<div class="abs email">Email Adress</div>
<div class="abs signup">SIGN UP</div>
<div class="abs social-ring" style="left:114px;top:3014px" aria-label="Social profile"></div>

<div class="abs foot-head" style="left:498px">About Us</div>
<p class="abs foot-text" style="left:498px;top:2886px;width:250px">Sed ut perspiciatis unde omnis iste natus error sit voluptataccusantium doloremque laudantium, totam rem aperiam, eaque ipsa quae ab illo inventore veritatis et quasarchitecto beatae vitae dicta sunt</p>

<div class="abs foot-head" style="left:798px">Navigate</div>
<div class="abs" style="left:798px;top:2882px">
  <div class="foot-link"><svg viewBox="0 0 10 10"><path d="M1 1l4 4-4 4M5 1l4 4-4 4" stroke="#ddd" stroke-width="1.5" fill="none"/></svg>Home</div>
  <div class="foot-link"><svg viewBox="0 0 10 10"><path d="M1 1l4 4-4 4M5 1l4 4-4 4" stroke="#ddd" stroke-width="1.5" fill="none"/></svg>About Us</div>
  <div class="foot-link"><svg viewBox="0 0 10 10"><path d="M1 1l4 4-4 4M5 1l4 4-4 4" stroke="#ddd" stroke-width="1.5" fill="none"/></svg>Videos</div>
  <div class="foot-link"><svg viewBox="0 0 10 10"><path d="M1 1l4 4-4 4M5 1l4 4-4 4" stroke="#ddd" stroke-width="1.5" fill="none"/></svg>Latest Blog</div>
  <div class="foot-link"><svg viewBox="0 0 10 10"><path d="M1 1l4 4-4 4M5 1l4 4-4 4" stroke="#ddd" stroke-width="1.5" fill="none"/></svg>Contact Us</div>
</div>
<div class="abs" style="left:961px;top:2882px">
  <div class="foot-link"><svg viewBox="0 0 10 10"><path d="M1 1l4 4-4 4M5 1l4 4-4 4" stroke="#ddd" stroke-width="1.5" fill="none"/></svg>Terms &amp; Conditions</div>
  <div class="foot-link"><svg viewBox="0 0 10 10"><path d="M1 1l4 4-4 4M5 1l4 4-4 4" stroke="#ddd" stroke-width="1.5" fill="none"/></svg>Privacy Policy</div>
  <div class="foot-link"><svg viewBox="0 0 10 10"><path d="M1 1l4 4-4 4M5 1l4 4-4 4" stroke="#ddd" stroke-width="1.5" fill="none"/></svg>Help Service</div>
  <div class="foot-link"><svg viewBox="0 0 10 10"><path d="M1 1l4 4-4 4M5 1l4 4-4 4" stroke="#ddd" stroke-width="1.5" fill="none"/></svg>FAQ</div>
  <div class="foot-link"><svg viewBox="0 0 10 10"><path d="M1 1l4 4-4 4M5 1l4 4-4 4" stroke="#ddd" stroke-width="1.5" fill="none"/></svg>Portfolio</div>
</div>

<div class="abs divider"></div>
<div class="abs copyright">© 2021 Loretta Dubrow. All Rights Reserved</div>

</body>
</html>
```